Stonebridge Building and Projects business cards

A business card with watermark background (construction work)

Company logo attached

Home improvement projects
House renovations
Bathroom and kitchen renovations
House extensions
New builds and granny flats

Director Omar Haddani
(Phone number)
omar@sbpbuilding.com.au
(Instagram logo) sbp_building

```html
<!DOCTYPE html>
<html lang="en">
<head>
<meta charset="utf-8">
<title>Stonebridge Building and Projects – Business Cards</title>
<link href="https://fonts.googleapis.com/css2?family=Arimo:wght@400;700&family=Questrial&family=Arvo&display=swap" rel="stylesheet">
<style>
  :root {
    --bg: #d6d6d8;
    --card-white: #ffffff;
    --card-black: #1f1f21;
    --band: #2a2a2c;
    --ink: #2b2b2d;
    --ink-soft: #4a4a4d;
    --blue: #2a6db5;
    --silver: #e4e4e6;
  }
  * { box-sizing: border-box; margin: 0; padding: 0; }
  html, body { width: 1200px; height: 800px; overflow: hidden; }
  body {
    background: var(--bg);
    display: flex;
    align-items: center;
    justify-content: center;
    gap: 40px;
    font-family: "Arimo", Arial, sans-serif;
  }
  .card {
    position: relative;
    width: 540px;
    height: 310px;
    border-radius: 18px;
    overflow: hidden;
    box-shadow: 0 10px 28px rgba(0,0,0,.18);
  }

  /* Front */
  .card-front { background: var(--card-white); color: var(--ink); }
  .holder { position: absolute; left: 34px; top: 46px; }
  .holder-name { font-weight: 700; font-size: 25px; letter-spacing: .5px; text-transform: uppercase; }
  .holder-role { color: var(--blue); font-size: 15px; margin-top: 2px; }

  .contact-band {
    position: absolute; left: 0; top: 112px;
    width: 350px; height: 96px;
    background: var(--band);
    clip-path: polygon(0 0, 300px 0, 350px 100%, 0 100%);
    padding: 12px 0 0 34px;
  }
  .contact-list { list-style: none; }
  .contact-list li {
    display: flex; align-items: center; gap: 8px;
    color: #fff; font-size: 13px; line-height: 18px;
  }
  .contact-list svg { width: 11px; height: 11px; flex: none; }

  .brand-front {
    position: absolute; right: 28px; top: 52px;
    display: flex; align-items: center; gap: 10px;
  }
  .brand-front .brand-name {
    color: var(--blue); font-weight: 700; font-size: 34px; letter-spacing: .5px;
  }
  .brand-square { width: 14px; height: 14px; background: var(--ink); flex: none; }

  .services {
    position: absolute; left: 34px; right: 28px; bottom: 30px;
    font-size: 13.5px; line-height: 20px; color: var(--ink-soft);
  }
  .services .sep {
    display: inline-block; width: 7px; height: 7px; margin: 0 7px 1px;
    background: var(--blue); vertical-align: middle;
  }
  .services .sep:first-child { margin-left: 0; }

  /* Back */
  .card-back {
    background: var(--card-black);
    display: flex; align-items: center; justify-content: center;
  }
  .lockup { text-align: center; color: var(--silver); font-family: "Questrial", "Century Gothic", sans-serif; }
  .lockup-head { display: flex; align-items: center; justify-content: center; gap: 12px; }
  .lockup-square { width: 16px; height: 16px; background: var(--blue); }
  .lockup-name { font-size: 40px; letter-spacing: 1px; }
  .lockup-rule { height: 1.5px; background: var(--blue); margin: 8px auto; width: 300px; }
  .lockup-sub { font-size: 11px; letter-spacing: 7px; text-transform: uppercase; }
  .tagline {
    display: inline-block; margin-top: 14px;
    font-family: "Arvo", Georgia, serif; font-size: 22px; color: var(--blue);
    border-bottom: 1.5px solid var(--blue); padding-bottom: 3px;
  }
</style>
</head>
<body>

<section class="card card-front" aria-label="Business card front">
  <div class="holder">
    <h1 class="holder-name">Omar Haddani</h1>
    <p class="holder-role">Director</p>
  </div>

  <div class="brand-front">
    <span class="brand-name">Stonebridge</span>
    <span class="brand-square"></span>
  </div>

  <div class="contact-band">
    <ul class="contact-list">
      <li>
        <svg viewBox="0 0 12 12" aria-hidden="true"><path d="M2.5 1 L4.5 1 L5.2 3.6 L4 4.6 Q5 7 7.4 8 L8.4 6.8 L11 7.5 L11 9.5 Q10.5 11 9 11 Q1 10 1 3 Q1 1.5 2.5 1 Z" fill="var(--blue)"/></svg>
        555-014-2278
      </li>
      <li>
        <svg viewBox="0 0 12 12" aria-hidden="true"><rect x="0.5" y="2" width="11" height="8" fill="var(--blue)"/><path d="M0.5 2 L6 6.5 L11.5 2" stroke="var(--band)" stroke-width="1" fill="none"/></svg>
        omar@sbpbuilding.com.au
      </li>
      <li>
        <svg viewBox="0 0 12 12" aria-hidden="true"><circle cx="6" cy="6" r="5" fill="none" stroke="var(--blue)" stroke-width="1.4"/><path d="M1 6 H11 M6 1 Q3 6 6 11 Q9 6 6 1" stroke="var(--blue)" stroke-width="1" fill="none"/></svg>
        sbpbuilding.com.au
      </li>
      <li>
        <svg viewBox="0 0 12 12" aria-hidden="true"><circle cx="6" cy="6" r="5" fill="var(--blue)"/></svg>
        sbp_building
      </li>
    </ul>
  </div>

  <p class="services">
    <span class="sep"></span>Home improvement projects<span class="sep"></span>House renovations<span class="sep"></span>House extensions<br>
    <span class="sep"></span>Bathroom &amp; kitchen renovations<span class="sep"></span>New builds &amp; granny flats
  </p>
</section>

<section class="card card-back" aria-label="Business card back">
  <div class="lockup">
    <div class="lockup-head">
      <span class="lockup-square"></span>
      <span class="lockup-name">Stonebridge</span>
    </div>
    <div class="lockup-rule"></div>
    <p class="lockup-sub">Building and Projects</p>
    <p class="tagline">Solid from the ground up!</p>
  </div>
</section>

</body>
</html>
```